Business Card Design Project

Keep it simple , using logo and colors that compliment. Logo on one side with complimentary back ground color. Other side, personal info with possible complimentary design/colors

Target Market(s)

we are a non for profit that will be seeking donations . Both monetary and in kind

Industry/Entity Type

Business

Font styles to use
Sans Serif

Colors

Designer to choose colors to be used in the design.

```html
<!DOCTYPE html>
<html lang="en">
<head>
<meta charset="utf-8">
<title>Open Hands Fund – Business Card</title>
<link rel="stylesheet" href="https://fonts.googleapis.com/css2?family=Open+Sans:wght@400;700&display=swap">
<style>
  :root {
    --navy: #2b3150;
    --yellow: #f2d00c;
    --paper: #f2f2f0;
    --backdrop: #e6e6e6;
    --ink: #2b3150;
    --ink-soft: #3d4260;
  }
  * { box-sizing: border-box; margin: 0; padding: 0; }
  html, body {
    width: 1200px;
    height: 675px;
    overflow: hidden;
    background: var(--backdrop);
    font-family: "Open Sans", Arial, sans-serif;
  }
  .canvas {
    position: relative;
    width: 1200px;
    height: 675px;
  }
  .card {
    position: absolute;
    width: 504px;
    height: 288px;
    box-shadow: 0 6px 18px rgba(0, 0, 0, 0.12);
    overflow: hidden;
  }

  /* Front: logo side */
  .card-front {
    left: 60px;
    top: 140px;
    background: var(--navy);
    display: flex;
    align-items: center;
    justify-content: center;
    gap: 18px;
  }
  .brand-mark {
    width: 46px;
    height: 46px;
    flex: none;
  }
  .brand-name {
    color: var(--yellow);
    font-weight: 400;
    font-size: 34px;
    letter-spacing: 0.5px;
    white-space: nowrap;
  }

  /* Back: personal info side */
  .card-back {
    left: 636px;
    top: 250px;
    background: var(--paper);
  }
  .card-back .brand {
    position: absolute;
    left: 30px;
    top: 118px;
    display: flex;
    align-items: center;
    gap: 10px;
  }
  .card-back .brand-mark { width: 26px; height: 26px; }
  .card-back .brand-name {
    color: var(--navy);
    font-size: 19px;
  }
  .contact {
    position: absolute;
    left: 262px;
    top: 72px;
    color: var(--ink);
  }
  .contact-name {
    font-weight: 700;
    font-size: 15px;
    line-height: 1.2;
  }
  .contact-role {
    font-size: 9px;
    color: var(--ink-soft);
    margin-bottom: 12px;
  }
  .contact-list {
    list-style: none;
    font-size: 10.5px;
    line-height: 1.65;
  }
  .contact-list li {
    display: flex;
    align-items: center;
    gap: 8px;
  }
  .contact-list svg {
    width: 10px;
    height: 10px;
    flex: none;
    fill: var(--ink);
  }
  .fax { margin-left: 8px; }
  .card-band {
    position: absolute;
    left: 0;
    right: 0;
    bottom: 0;
    height: 12px;
    background: var(--navy);
  }
</style>
</head>
<body>
<main class="canvas">

  <section class="card card-front" aria-label="Card front">
    <svg class="brand-mark" viewBox="0 0 46 46" aria-hidden="true">
      <circle cx="23" cy="23" r="20" fill="none" stroke="var(--yellow)" stroke-width="4"/>
    </svg>
    <span class="brand-name">Open Hands Fund</span>
  </section>

  <section class="card card-back" aria-label="Card back">
    <div class="brand">
      <svg class="brand-mark" viewBox="0 0 26 26" aria-hidden="true">
        <circle cx="13" cy="13" r="12" fill="var(--navy)"/>
      </svg>
      <span class="brand-name">Open Hands Fund</span>
    </div>

    <div class="contact">
      <p class="contact-name">Your Long Name</p>
      <p class="contact-role">Owner / President</p>
      <ul class="contact-list">
        <li>
          <svg viewBox="0 0 10 10" aria-hidden="true"><path d="M5 0a3.3 3.3 0 0 0-3.3 3.3C1.7 5.8 5 10 5 10s3.3-4.2 3.3-6.7A3.3 3.3 0 0 0 5 0zm0 4.6a1.3 1.3 0 1 1 0-2.6 1.3 1.3 0 0 1 0 2.6z"/></svg>
          Your Commercial or office address
        </li>
        <li>
          <svg viewBox="0 0 10 10" aria-hidden="true"><path d="M1 3.5C1 2 3 1 5 1s4 1 4 2.5V4.5H7V3.6C6.4 3.3 5.7 3.2 5 3.2s-1.4.1-2 .4v.9H1zM2 5h6l1 4H1z"/></svg>
          00.00.00.0000
          <svg class="fax" viewBox="0 0 10 10" aria-hidden="true"><path d="M2.5 0h5v3h-5zM0 3.8h10V8H8v2H2V8H0zm3 3.2v2h4V7z"/></svg>
          00.00.00.0000
        </li>
        <li>
          <svg viewBox="0 0 10 10" aria-hidden="true"><path d="M0 2h10v.6L5 5.6 0 2.6zm0 1.7l5 3 5-3V8H0z"/></svg>
          yourname@yourwebsite.com
        </li>
        <li>
          <svg viewBox="0 0 10 10" aria-hidden="true"><path d="M5 0a5 5 0 1 0 0 10A5 5 0 0 0 5 0zm3.9 4.4H7.1A7 7 0 0 0 6.3 1a4 4 0 0 1 2.6 3.4zM5 1.1c.6.8 1 2 1.1 3.3H3.9C4 3.1 4.4 1.9 5 1.1zM3.7 1a7 7 0 0 0-.8 3.4H1.1A4 4 0 0 1 3.7 1zM1.1 5.6h1.8A7 7 0 0 0 3.7 9a4 4 0 0 1-2.6-3.4zM5 8.9c-.6-.8-1-2-1.1-3.3h2.2C6 6.9 5.6 8.1 5 8.9zM6.3 9a7 7 0 0 0 .8-3.4h1.8A4 4 0 0 1 6.3 9z"/></svg>
          www.yourwebsite.com
        </li>
      </ul>
    </div>

    <div class="card-band"></div>
  </section>

</main>
</body>
</html>
```